Business card for Luxury Portable Restroom Trailer company

We are a Luxury Portable Restroom Trailer Company Called FALCRIDGE HIRES. Based in Orange County California. We provide portable restroom trailers for events, such as, Weddings, Concerts, Charity events, Sporting events, Tournaments, Corporate events, ect. We rent and Sell the Luxury restrooms. Our colors are white, grey, and Orange. As you will see in the logo we uploaded.
There are 2 people in the company so the names and titles will change for the 3 people but card will remain the same. Here is the information for each Person: Dwight Penner CFO 555 318-0476
next Person: Leon Marchetti VP 555 318-0476
Next Person: Owen Marchetti CEO 555 318-0476
Information to include on the card: Luxury Restroom Trailers Rental and Sales. Weddings, Concerts, Charity, Sporting and Corp. Events.

```html
<!DOCTYPE html>
<html lang="en">
<head>
<meta charset="utf-8">
<title>Falcridge Hires – Business Card</title>
<link rel="stylesheet" href="https://fonts.googleapis.com/css2?family=Barlow+Semi+Condensed:wght@400;500;600&display=swap">
<style>
  :root {
    --orange: #ef7b3d;
    --orange-soft: #f0864b;
    --grey: #5e6266;
    --grey-light: #8a8d90;
    --white: #ffffff;
    --paper: #f6f6f6;
    --backdrop: #e6e6e6;
  }
  * { box-sizing: border-box; margin: 0; padding: 0; }
  html, body {
    width: 1200px; height: 1200px; overflow: hidden;
    background: var(--backdrop);
    font-family: "Barlow Semi Condensed", "Arial Narrow", sans-serif;
  }
  .sheet {
    width: 1200px; height: 1200px;
    display: flex; flex-direction: column; align-items: center; justify-content: center;
    gap: 80px;
  }
  .card {
    position: relative;
    width: 700px; height: 400px;
    border-radius: 36px;
    overflow: hidden;
    box-shadow: 0 14px 30px rgba(0,0,0,0.14);
  }

  /* Front */
  .card--front { background: var(--orange); }
  .front-pattern {
    position: absolute; inset: 0;
    background: radial-gradient(circle at 70% 70%, var(--orange-soft), var(--orange) 70%);
  }
  .front-brand {
    position: absolute; left: 470px; top: 250px;
    display: flex; align-items: center; gap: 12px;
  }
  .front-brand__circle {
    width: 64px; height: 64px; border-radius: 50%;
    border: 6px solid var(--grey);
  }
  .front-brand__name {
    font-weight: 600; font-size: 20px; letter-spacing: 1px;
    color: var(--grey); line-height: 1.05;
  }

  /* Back */
  .card--back { background: var(--paper); }
  .back-decor {
    position: absolute; left: -120px; top: 20px;
    width: 360px; height: 360px; border-radius: 50%;
    background: radial-gradient(circle, #f1f1f1, var(--paper) 70%);
  }
  .back-content {
    position: absolute; left: 200px; top: 62px; width: 420px;
    display: flex; flex-direction: column; align-items: center;
  }
  .brand-name {
    font-weight: 600; font-size: 26px; letter-spacing: 2px;
    color: var(--grey);
  }
  .person {
    margin-top: 30px;
    font-size: 24px; color: var(--grey);
    display: flex; align-items: baseline; gap: 10px;
  }
  .person__name { font-weight: 600; letter-spacing: 0.5px; }
  .person__sep { font-size: 16px; color: var(--grey-light); }
  .person__title { font-weight: 400; color: var(--grey-light); }
  .phone {
    margin-top: 4px;
    font-weight: 500; font-size: 50px; letter-spacing: 1px;
    color: var(--orange);
  }
  .divider {
    margin-top: 18px; width: 120px;
    border-top: 1.5px dotted var(--grey-light);
  }
  .services {
    margin-top: 22px; text-align: center;
    font-size: 14px; line-height: 1.6; letter-spacing: 0.5px;
    color: var(--grey); text-transform: uppercase;
  }
</style>
</head>
<body>
<main class="sheet">
  <section class="card card--front" aria-label="Card front">
    <div class="front-pattern" role="img" aria-label="Faint repeated brand pattern in tonal orange"></div>
    <div class="front-brand">
      <span class="front-brand__circle"></span>
      <span class="front-brand__name">FALCRIDGE<br>HIRES</span>
    </div>
  </section>

  <section class="card card--back" aria-label="Card back">
    <div class="back-decor" role="img" aria-label="Large faint brand decoration"></div>
    <div class="back-content">
      <div class="brand-name">FALCRIDGE HIRES</div>
      <div class="person">
        <span class="person__name">DWIGHT PENNER</span>
        <span class="person__sep">|</span>
        <span class="person__title">CFO</span>
      </div>
      <div class="phone">555 318-0476</div>
      <div class="divider"></div>
      <p class="services">Luxury restroom trailers rental and sales.<br>Weddings, concerts, charity, sporting and corp. events.</p>
    </div>
  </section>
</main>
</body>
</html>
```